Blow Dry Bar Business Cards

These cards must be eye catching and modern.
You must be willing to work fast and make changes.

Winner will be offered other projects

Files 1 THIS IS THE STYLE CARDS I AM INTRESTED IN!!!
Please be creative, I am paying for my own eye catching design. I need files to be nexa press ready.

COLORS THAT ARE PAINTED INSIDE MY SHOP:
- - - http://www.quorvelpaint.example/en/explore-colors/painter/color-selector.html?colors=4007-3C

- - - http://www.brandivex.example/color/paint-colors/hidden-corridor-d58-2

I want the business cards sleek and modern if you use the logo please correct imperfections. I added the part that says Blow Dry Bar (see website).
Do not be afraid to separate the blow dryer from the name to make the cards look like the file with the pink elephant.

SHOULD INCLUDE
*Blow Dryer (we are a blow dry bar not a salon we do not cut or color so do not include sheers of any kind)
*BUSINESS NAME: Simply Swept Upward - Blow Dry Bar (PLEASE SEE MY WEBSITE)
* Website: SIMPLYSWEPTUPWARD.EXAMPLE
*Phone number (555) 014-2763
Updates

Nexa press said it can be submitted in JPG

http://www.brandivex.example/color/paint-colors/hidden-corridor-d58-2 http://www.quorvelpaint.example/en/explore-colors/painter/color-selector.html?colors=4007-3C ^^^^ These links will take you to the color paint that is painted inside my shop.

Target Market(s)

AGES 18 - 55 WOMEN
HIGH END MARKET

Industry/Entity Type

Salon

Requirements
Must have
• SEE COLOR EXAMPLE FILE
BLOW DRYER
UNIQUE
I LIKE THE CARD WITH THE PINK ELEPHANT THE BEST
Nice to have
• BE AS CREATIVE AND MODERN AS POSSIBLE DO NOT COPY ANY OF THE CARDS BELOW.
Should not have
• SCISSORS
PINK

```html
<!DOCTYPE html>
<html lang="en">
<head>
<meta charset="utf-8">
<title>Blow Dry Bar Business Cards</title>
<link rel="stylesheet" href="https://fonts.googleapis.com/css2?family=Josefin+Sans:wght@300;400&display=swap">
<style>
  :root {
    --backdrop: #d8d3ca;
    --card-edge: #3b3b3b;
    --card-mid: #5f5f5f;
    --card-glow: #8c8c8c;
    --ink-light: #f4f4f4;
    --ink-soft: #e2e2e2;
    --band: #e9e9e9;
    --band-ink: #4a4a4a;
  }
  html, body {
    margin: 0;
    width: 1200px;
    height: 885px;
    overflow: hidden;
    background: var(--backdrop);
  }
  .stage {
    position: relative;
    width: 1200px;
    height: 885px;
  }
  .card {
    position: absolute;
    top: 292px;
    width: 520px;
    height: 300px;
    border-radius: 16px;
    overflow: hidden;
    box-shadow: 0 10px 26px rgba(0,0,0,.28);
    font-family: "Josefin Sans", sans-serif;
    color: var(--ink-light);
  }
  .card--front { left: 60px; }
  .card--back { left: 620px; }
  .card__texture {
    position: absolute;
    inset: 0;
    background: radial-gradient(ellipse at 50% 42%, var(--card-glow) 0%, var(--card-mid) 48%, var(--card-edge) 100%);
  }
  .rule {
    position: absolute;
    height: 1px;
    background: var(--ink-soft);
  }
  .front__title {
    position: absolute;
    left: 36px;
    top: 30px;
    margin: 0;
    font-weight: 300;
    font-size: 46px;
    letter-spacing: .5px;
  }
  .front__title-rule { left: 36px; right: 0; top: 100px; }
  .front__names {
    position: absolute;
    left: 210px;
    top: 114px;
    font-weight: 300;
    font-size: 17px;
  }
  .front__names-rule { left: 36px; width: 160px; top: 124px; }
  .front__contact {
    position: absolute;
    left: 210px;
    top: 146px;
    margin: 0;
    padding: 0;
    list-style: none;
    font-weight: 300;
    font-size: 14px;
    letter-spacing: .6px;
    line-height: 26px;
  }
  .front__band {
    position: absolute;
    left: 0;
    right: 0;
    bottom: 0;
    height: 38px;
    background: var(--band);
    color: var(--band-ink);
    font-size: 13.5px;
    letter-spacing: .8px;
    line-height: 40px;
    text-align: center;
    font-weight: 400;
  }
  .back__brand {
    position: absolute;
    left: 0;
    right: 0;
    top: 96px;
    display: flex;
    justify-content: center;
    align-items: center;
    gap: 14px;
  }
  .back__name {
    margin: 0;
    font-weight: 300;
    font-size: 38px;
    color: var(--ink-light);
  }
  .back__dot {
    width: 22px;
    height: 22px;
    border-radius: 50%;
    background: var(--ink-light);
  }
  .back__web {
    position: absolute;
    left: 0;
    right: 0;
    top: 176px;
    text-align: center;
    font-weight: 300;
    font-size: 13px;
    letter-spacing: 1px;
  }
  .back__rule { left: 210px; width: 100px; top: 214px; }
</style>
</head>
<body>
<main class="stage">

  <section class="card card--front">
    <div class="card__texture" role="img" aria-label="Soft grey damask pattern across the card"></div>
    <h1 class="front__title">Blow Dry Bar</h1>
    <div class="rule front__title-rule"></div>
    <div class="rule front__names-rule"></div>
    <div class="front__names">Marisol&amp;Tee</div>
    <ul class="front__contact">
      <li>(555) 014-2763</li>
      <li>SIMPLYSWEPTUPWARD.EXAMPLE</li>
      <li>INFO@SIMPLYSWEPTUPWARD.EXAMPLE</li>
    </ul>
    <div class="front__band">280 HERON BEND ROAD SUITE 9 MAPLE HOLLOW, TEXAS 70000</div>
  </section>

  <section class="card card--back">
    <div class="card__texture" role="img" aria-label="Soft grey damask pattern across the card"></div>
    <div class="back__brand">
      <h2 class="back__name">Simply Swept Upward</h2>
      <span class="back__dot"></span>
    </div>
    <div class="back__web">SIMPLYSWEPTUPWARD.EXAMPLE</div>
    <div class="rule back__rule"></div>
  </section>

</main>
</body>
</html>
```